The Lantern and the Orchard: Notes From Quiet Mornings

We need a book cover/spine and back cover for a multi author book called the Lantern and The Orchard: Notes from Quiet Mornings. This will be a collection of stories from women who major transformational stories to tell. They embark on a voyage, find themselves in uncharted territory, find friends or allies and in the end find themselves back home to themselves. I want this book cover to feel fun of wonder, adventure, intrigue with a a dainty energy. I have uploaded some images for inspiration but not to use in the design because they are not images I have permission to use.

```html
<!DOCTYPE html>
<html lang="en">
<head>
<meta charset="utf-8">
<title>The Lantern and the Orchard — Cover Wrap</title>
<link rel="stylesheet" href="https://fonts.googleapis.com/css2?family=Kaushan+Script&family=Arimo:wght@400;700&family=Oswald:wght@600&display=swap">
<style>
  :root {
    --sky-top: #a9e3f4;
    --sky-mid: #c4ecf8;
    --haze: #eef6fa;
    --field-light: #e3b43a;
    --field: #d59e1c;
    --field-deep: #a8781a;
    --title-front: #1d4a5f;
    --title-back: #3e6c7e;
    --subtitle: #6f7a80;
    --body-text: #2e3438;
    --white: #ffffff;
  }
  * { margin: 0; padding: 0; box-sizing: border-box; }
  html, body { width: 1200px; height: 778px; overflow: hidden; background: var(--white); }
  .cover-wrap { position: relative; width: 1200px; height: 778px; overflow: hidden; }

  .scene-photo {
    position: absolute; inset: 0;
    background:
      radial-gradient(ellipse 260px 200px at 600px 260px, rgba(255,255,255,.55), rgba(255,255,255,0) 70%),
      linear-gradient(to bottom,
        var(--sky-top) 0%, var(--sky-mid) 30%, var(--haze) 47%,
        var(--field-light) 51%, var(--field) 68%, var(--field-deep) 100%);
  }

  .script { font-family: "Kaushan Script", cursive; font-weight: 400; }
  .caps-and { font-family: "Arimo", sans-serif; font-weight: 700; }

  /* Back cover */
  .back-title {
    position: absolute; left: 50px; top: 138px;
    color: var(--title-back); font-size: 44px; line-height: 1; white-space: nowrap;
  }
  .back-title .caps-and { font-size: 20px; margin: 0 4px; }
  .blurb {
    position: absolute; left: 48px; top: 234px;
    font-family: "Arimo", sans-serif; font-size: 17px; color: var(--body-text);
  }
  .blurb p { height: 36px; line-height: 26px; padding-left: 7px; white-space: nowrap; }
  .blurb p.lead { padding-left: 0; }
  .blurb p.lead strong { font-weight: 700; }
  .blurb .break { height: 36px; }

  /* Spine */
  .spine-title {
    position: absolute; left: 584px; top: 305px;
    writing-mode: vertical-rl;
    color: var(--white); font-size: 22px; white-space: nowrap;
  }
  .spine-title .caps-and { font-size: 11px; margin: 3px 0; }

  /* Front cover */
  .front-title { position: absolute; left: 690px; top: 62px; color: var(--title-front); }
  .front-title .line { display: block; font-size: 92px; line-height: 1.2; white-space: nowrap; }
  .front-title .line-one { margin-left: 30px; }
  .front-title .line-two { margin-left: 36px; }
  .front-title .caps-and {
    position: absolute; left: 2px; top: 126px; font-size: 32px; color: #2c3d46;
  }
  .subtitle {
    position: absolute; left: 700px; width: 440px; top: 333px; text-align: center;
    font-family: "Oswald", sans-serif; font-weight: 600; font-size: 33px;
    color: var(--subtitle); letter-spacing: .3px; white-space: nowrap;
  }
  .authors {
    position: absolute; left: 861px; top: 600px; list-style: none;
    font-family: "Arimo", sans-serif; font-weight: 700; font-size: 17px; color: var(--white);
  }
  .authors li { height: 36px; line-height: 28px; }
</style>
</head>
<body>
<main class="cover-wrap">
  <div class="scene-photo" role="img" aria-label="Photograph: a woman with long dark hair seen from behind, walking through a field of yellow flowers under a pale blue sky"></div>

  <section class="back-cover">
    <h2 class="back-title"><span class="script">The Lantern</span> <span class="caps-and">AND</span> <span class="script">the Orchard</span></h2>
    <div class="blurb">
      <p class="lead"><strong>Lorem</strong> ipsum lorem ipsum lorem ipsum lorem ipsum</p>
      <p>lorem ipsum lorem ipsum lorem ipsum lorem ipsum</p>
      <p>lorem ipsum lorem ipsum lorem ipsum lorem ipsum</p>
      <p>lorem ipsum lorem ipsum lorem ipsum lorem ipsum</p>
      <div class="break"></div>
      <p>lorem ipsum lorem ipsum lorem ipsum lorem ipsum</p>
      <p>lorem ipsum lorem ipsum lorem ipsum lorem ipsum</p>
      <p>lorem ipsum lorem ipsum lorem ipsum lorem ipsum</p>
      <p>lorem ipsum lorem ipsum lorem ipsum lorem ipsum</p>
    </div>
  </section>

  <aside class="spine">
    <p class="spine-title"><span class="script">The Lantern</span><span class="caps-and">AND</span><span class="script">the Orchard</span></p>
  </aside>

  <section class="front-cover">
    <h1 class="front-title">
      <span class="line line-one script">The Lantern</span>
      <span class="caps-and">AND</span>
      <span class="line line-two script">the Orchard</span>
    </h1>
    <p class="subtitle">NOTES FROM QUIET MORNINGS</p>
    <ul class="authors">
      <li>AUTHER NO. 1</li>
      <li>AUTHER NO. 2</li>
      <li>AUTHER NO. 3</li>
      <li>AUTHER NO. 4</li>
    </ul>
  </section>
</main>
</body>
</html>
```